DRALVO 2020

I have a front picture for the CD; I have all of the info for the back cover; I need someone to put my idea together with the correct specs; I require a very FAST TURN AROUND!!! I need to get this project to the CD replicator by next week ASAP...

```html
<!DOCTYPE html>
<html lang="en">
<head>
<meta charset="utf-8">
<title>DRALVO 2020 – Album Covers</title>
<link href="https://fonts.googleapis.com/css2?family=Poppins:wght@500;700;800;900&family=Playfair+Display:wght@800;900&display=swap" rel="stylesheet">
<style>
  :root {
    --bg: #5e5e5e;
    --navy: #13284f;
    --navy-deep: #0b1d3f;
    --navy-light: #2c4a80;
    --red: #c8141c;
    --red-deep: #9e0f16;
    --red-bright: #e8202a;
    --white: #ffffff;
    --silver: #d9dbde;
    --silver-dark: #9ea2a8;
    --flag-blue: #2136a8;
  }
  * { margin: 0; padding: 0; box-sizing: border-box; }
  html, body { width: 1200px; height: 641px; overflow: hidden; }
  body {
    background: var(--bg);
    position: relative;
    font-family: "Poppins", Arial, sans-serif;
  }

  /* Front cover */
  .front-cover {
    position: absolute; left: 68px; top: 68px;
    width: 510px; height: 491px;
    background: var(--red);
    overflow: hidden;
  }
  .front-header {
    position: absolute; left: 0; top: 0; width: 100%; height: 151px;
    background: radial-gradient(ellipse at 50% 100%, var(--navy-light) 0%, var(--navy) 55%, var(--navy-deep) 100%);
    text-align: center;
  }
  .front-title {
    position: absolute; left: 0; right: 0; top: 4px;
    font-weight: 900; font-size: 104px; line-height: 1;
    letter-spacing: -3px; color: #ececec;
    text-shadow: 0 3px 4px rgba(0,0,0,.45);
  }
  .front-tagline {
    position: absolute; left: 0; right: 0; top: 112px;
    font-weight: 600; font-size: 17px; letter-spacing: 4.2px;
    color: #e9e9e9;
  }
  .silver-band {
    position: absolute; left: 0; width: 100%;
    background: linear-gradient(var(--white), var(--silver) 50%, var(--silver-dark));
  }
  .silver-band.top { top: 151px; height: 13px; }
  .front-photo {
    position: absolute; left: 0; top: 164px; width: 100%; height: 247px;
    background: linear-gradient(180deg, #d8dce8 0%, #c33a44 35%, #f1e6e6 55%, #b8222b 75%, #e9d8d8 100%);
    overflow: hidden;
  }
  .front-photo::before {
    content: ""; position: absolute; left: 0; top: 0; width: 45%; height: 60%;
    background: linear-gradient(135deg, var(--flag-blue), #3a56d0);
  }
  .front-year {
    position: absolute; left: -6px; top: -4px; width: 522px;
    font-weight: 800; font-size: 196px; line-height: 1;
    letter-spacing: -6px; text-align: center;
    color: rgba(255,255,255,.55);
  }
  .front-bottom-frame {
    position: absolute; left: 0; top: 405px; width: 510px; height: 28px;
  }
  .front-artist {
    position: absolute; left: 0; right: 0; top: 432px;
    text-align: center;
    font-family: "Playfair Display", Georgia, serif;
    font-weight: 900; font-size: 31px; letter-spacing: 2px;
    color: #f3f0ee;
  }
  .front-cover .red-fill {
    position: absolute; left: 0; top: 411px; width: 100%; height: 80px;
    background: linear-gradient(var(--red-bright), var(--red) 40%, var(--red-deep));
  }

  /* Back cover */
  .back-cover {
    position: absolute; left: 653px; top: 77px;
    width: 481px; height: 482px;
    overflow: hidden;
  }
  .back-header {
    position: absolute; left: 0; top: 0; width: 100%; height: 79px;
    background: var(--navy-deep);
    text-align: center;
  }
  .back-title {
    position: absolute; left: 0; right: 0; top: 2px;
    font-weight: 800; font-size: 49px; line-height: 1.1;
    letter-spacing: -1px; color: var(--white);
  }
  .back-artist {
    position: absolute; left: 0; right: 0; top: 49px;
    font-family: "Playfair Display", Georgia, serif;
    font-weight: 900; font-size: 25px; line-height: 1;
    letter-spacing: 2px; color: var(--red-bright);
  }
  .back-photo {
    position: absolute; left: 0; top: 79px; width: 100%; height: 403px;
    background: linear-gradient(160deg, #5a4f57 0%, #7b3440 25%, #1f3b8a 50%, #6b5a5e 75%, #8a4a50 100%);
  }
  .track-list {
    position: absolute; left: 25px; top: 100px;
    list-style: none;
  }
  .track-list li {
    height: 32px;
    font-weight: 800; font-size: 12.5px; line-height: 18px;
    color: var(--white);
    text-shadow: 0 1px 2px rgba(0,0,0,.6);
  }
  .label-box {
    position: absolute; left: 334px; top: 394px;
    width: 52px; height: 25px; background: var(--white);
  }
  .liner-note {
    position: absolute; left: 20px; top: 425px; width: 275px;
    font-weight: 500; font-size: 7.4px; line-height: 8.8px;
    color: var(--white);
  }
</style>
</head>
<body>

  <section class="front-cover">
    <div class="front-header">
      <h1 class="front-title">DRALVO</h1>
      <p class="front-tagline">MUSIC THAT RINGS TRUTH</p>
    </div>
    <div class="silver-band top"></div>
    <div class="front-photo" role="img" aria-label="Candidate in suit with open arms before a waving American flag">
      <span class="front-year">2020</span>
    </div>
    <div class="red-fill"></div>
    <svg class="front-bottom-frame" viewBox="0 0 510 28" aria-hidden="true">
      <defs>
        <linearGradient id="silverGrad" x1="0" y1="0" x2="0" y2="1">
          <stop offset="0" stop-color="#ffffff"/>
          <stop offset="1" stop-color="#a2a6ac"/>
        </linearGradient>
      </defs>
      <path d="M0 0 H510 V8 H425 L410 22 H100 L85 8 H0 Z" fill="url(#silverGrad)"/>
    </svg>
    <p class="front-artist">Leo Marzetti</p>
  </section>

  <section class="back-cover">
    <div class="back-header">
      <h2 class="back-title">DRALVO 2020</h2>
      <p class="back-artist">Leo Marzetti</p>
    </div>
    <div class="back-photo" role="img" aria-label="Collage of rally crowds with signs, flags and the candidate waving"></div>
    <ol class="track-list">
      <li>1. DRALVO DERANGEMENT SYNDROME</li>
      <li>2. WOW THING</li>
      <li>3. STAR SPANGLED BANNER</li>
      <li>4. AMERICA IS BEAUTIFUL</li>
      <li>5. LET DRALVO BE DRALVO</li>
      <li>6. I BELIEVE IN HIM</li>
      <li>7. HE'S SO BAD</li>
      <li>8. NEVER DRALVO BLUES</li>
      <li>9. MAR DEL SOL</li>
    </ol>
    <div class="label-box"></div>
    <p class="liner-note">Lorem ipsum dolor sit amet, consectetur adipiscing elit, sed do eiusmod tempor incididunt ut labore et dolore magna aliqua. Ut enim ad minim veniam, quis nostrud exercitation ullamco laboris nisi ut aliquip ex ea commodo consequat.</p>
  </section>

</body>
</html>
```